Multi-Line Insurance PPC Landing Page - Conversion optimized.

We have a PPC landing page used for the general population to get an insurance quote through an agent's site.

We'd like to improve the page for PPC traffic, make it more conversion friendly.

Site should be a single long page.

We will dynamically change the form and headlines on the page depending on what insurance "line" is being called. ie, Lift, Auto, Home, Business.

The enclosed AI file has all of the raw elements we need. We're looking to enhance the design and conversion ability.

Target Market(s)

General public needed insurance services.

Industry/Entity Type

Insurance Broker

Number of Pages Required

1 page

Font styles to use
Sans Serif

Requirements
Must have
• Form, agent picture, name, address.

```html
<!DOCTYPE html>
<html lang="en">
<head>
<meta charset="utf-8">
<title>Insurance Agent – Get a Quote</title>
<link rel="stylesheet" href="https://fonts.googleapis.com/css2?family=Open+Sans:wght@400;600;700&display=swap">
<style>
:root{
  --blue:#1f5fa8;
  --navy:#17457f;
  --navy-dark:#123868;
  --green:#2f7d1c;
  --text:#4a4a4a;
  --muted:#8a8a8a;
  --line:#d6d6d6;
  --band:#ebebeb;
  --panel:#f4f4f4;
  --white:#ffffff;
}
*{box-sizing:border-box;margin:0;padding:0}
html,body{width:1200px;height:2184px;overflow:hidden}
body{font-family:"Open Sans",Arial,sans-serif;color:var(--text);background:var(--white);position:relative}
button{font-family:inherit}
section,header,footer{position:absolute;left:0;width:1200px}

/* header */
.site-header{top:0;height:88px;display:flex;align-items:center;justify-content:space-between;padding:0 120px;border-bottom:3px solid var(--blue)}
.brand{font-size:34px;font-weight:700;color:var(--blue);letter-spacing:-.5px}
.header-phone{display:flex;align-items:center;gap:12px}
.header-phone .label{font-size:12px;color:var(--muted);display:block}
.header-phone .number{font-size:20px;font-weight:700;color:var(--blue)}

/* hero */
.hero{top:88px;height:440px;overflow:hidden}
.hero-photo{position:absolute;inset:0;background:linear-gradient(120deg,#f2f5f8 0%,#cfd9e4 35%,#8fa4bb 60%,#2c3d55 100%)}
.hero-caption{position:absolute;left:120px;top:212px;width:440px;height:70px;padding:0 24px;display:flex;align-items:center;background:rgba(20,40,70,.78);border-left:6px solid var(--blue)}
.hero-caption h1{font-size:36px;font-weight:700;color:var(--white);line-height:1;white-space:nowrap}
.btn{display:inline-block;background:var(--green);color:var(--white);font-weight:700;font-size:18px;padding:12px 26px;text-transform:uppercase;border:none}
.hero .btn{position:absolute;left:120px;top:298px}
.slider-arrow{position:absolute;top:235px;width:32px;height:50px;background:rgba(60,60,60,.75);display:flex;align-items:center;justify-content:center}
.slider-arrow.prev{left:0}.slider-arrow.next{right:0}

/* lines */
.lines{top:528px;height:300px}
.line-card{position:absolute;top:60px;width:212px;height:225px;background:var(--white);box-shadow:0 3px 10px rgba(0,0,0,.18);text-align:center;padding:64px 14px 0}
.line-icon{position:absolute;left:66px;top:-50px;width:80px;height:80px;border-radius:50%;background:var(--blue);border:4px solid var(--white);box-shadow:0 2px 6px rgba(0,0,0,.25);display:flex;align-items:center;justify-content:center}
.line-card h3{font-size:24px;font-weight:700;color:#333;margin-bottom:8px}
.line-card p{font-size:12px;line-height:1.45;color:var(--muted);height:70px}
.line-card .btn{font-size:12px;padding:6px 16px;margin-top:6px}

/* quote */
.quote{top:860px;height:395px;background:var(--panel)}
.agent-card{position:absolute;left:120px;top:20px;width:322px;height:350px;background:var(--white);border:1px solid var(--line);text-align:center;padding-top:20px}
.agent-photo{width:164px;height:164px;border-radius:50%;margin:0 auto 16px;border:5px solid var(--blue);background:linear-gradient(160deg,#d9e1ea,#7d8fa6)}
.agent-name{font-size:24px;font-weight:600;color:#333}
.agent-phone{font-size:18px;color:#333;display:flex;align-items:center;justify-content:center;gap:8px;margin:6px 0 12px}
.agent-address{font-size:14px;line-height:1.4;color:#555}
.quote-form{position:absolute;left:462px;top:20px;width:618px;height:350px;background:var(--white);border:1px solid var(--line);padding:16px 24px}
.quote-form h2{font-size:26px;font-weight:700;color:var(--blue);padding-bottom:10px;border-bottom:1px solid var(--line);margin-bottom:14px}
.quote-form h2 span{color:#333}
.form-grid{display:grid;grid-template-columns:1fr 1fr;column-gap:24px;row-gap:10px}
.field label{display:block;font-size:12px;color:#555;margin-bottom:4px}
.input{height:28px;border:1px solid var(--line);background:#fafafa;font-size:12px;color:var(--muted);display:flex;align-items:center;justify-content:space-between;padding:0 8px}
.input-row{display:flex;gap:8px}.input-row .input{flex:1}
.quote-form .btn{margin-top:14px;font-size:14px;padding:7px 28px}

/* about */
.about{top:1268px;height:170px;text-align:center;padding:0 140px}
.section-title{font-size:28px;font-weight:600;color:var(--blue)}
.section-title span{color:#333}
.about hr{width:920px;margin:10px auto 12px;border:none;border-top:1px solid var(--line)}
.about p{font-size:14px;line-height:1.55;color:#555}

/* reviews */
.reviews{top:1445px;height:370px;background:var(--band)}
.reviews-head{position:absolute;top:26px;left:0;width:1200px;display:flex;justify-content:center;align-items:center;gap:26px}
.round-arrow{width:30px;height:30px;border-radius:50%;background:var(--white);display:flex;align-items:center;justify-content:center}
.review{position:absolute;top:90px;width:440px}
.review-box{background:var(--white);padding:22px 24px 22px 56px;position:relative;border:1px solid var(--line)}
.review-box .qmark{position:absolute;left:18px;top:10px;font-size:48px;font-weight:700;color:#bbb;line-height:1}
.review-box p{font-size:13px;line-height:1.6;font-style:italic;color:#666}
.reviewer{display:flex;align-items:center;gap:18px;margin:16px 0 0 20px}
.reviewer-photo{width:64px;height:64px;border-radius:50%;border:3px solid var(--white);background:linear-gradient(160deg,#c9d2dc,#6f8196)}
.reviewer-name{font-size:14px;font-weight:600;color:var(--green)}

/* partners */
.partners{top:1825px;height:200px;text-align:center}
.partners .section-title{display:inline-block;padding:4px 20px;border-top:2px solid var(--blue);border-bottom:2px solid var(--blue)}
.partner-row{position:absolute;top:100px;left:100px;width:1000px;display:flex;justify-content:space-between;align-items:center}
.partner{display:flex;align-items:center;gap:8px;font-size:26px;font-weight:700;color:#333}
.partner i{width:16px;height:16px;background:var(--blue);display:inline-block}

/* footer */
.site-footer{top:2030px;height:154px;background:var(--blue);color:#dfe8f5;text-align:center}
.site-footer h4{font-size:16px;font-weight:700;color:var(--white);padding-top:14px}
.site-footer p{font-size:12px;line-height:1.5;width:920px;margin:6px auto 0}
.footer-bar{position:absolute;left:0;bottom:0;width:1200px;height:40px;background:var(--navy-dark);display:flex;align-items:center;justify-content:space-between;padding:0 120px}
.footer-bar small{font-size:12px}
.footer-bar strong{font-size:22px;font-weight:600;color:#c8d6ea}
</style>
</head>
<body>

<header class="site-header">
  <div class="brand">Insurance Agent</div>
  <div class="header-phone">
    <svg width="34" height="34" viewBox="0 0 24 24"><circle cx="12" cy="12" r="11" fill="none" stroke="#1f5fa8" stroke-width="1.5"/><path d="M8 6.5l2 0 1 3-1.3 1a7 7 0 003.8 3.8l1-1.3 3 1v2a1.5 1.5 0 01-1.6 1.5A10 10 0 016.5 8.1 1.5 1.5 0 018 6.5z" fill="#1f5fa8"/></svg>
    <div><span class="label">Get a quick quote by phone</span><span class="number">(555) 240-7316</span></div>
  </div>
</header>

<section class="hero">
  <div class="hero-photo" role="img" aria-label="Photo of a business handshake between two people in suits"></div>
  <div class="hero-caption"><h1>Business Insurance</h1></div>
  <a class="btn">Get a Quote!</a>
  <div class="slider-arrow prev"><svg width="14" height="20" viewBox="0 0 14 20"><path d="M11 2L3 10l8 8" stroke="#fff" stroke-width="3" fill="none"/></svg></div>
  <div class="slider-arrow next"><svg width="14" height="20" viewBox="0 0 14 20"><path d="M3 2l8 8-8 8" stroke="#fff" stroke-width="3" fill="none"/></svg></div>
</section>

<section class="lines">
  <div class="line-card" style="left:148px">
    <div class="line-icon"><svg width="40" height="40" viewBox="0 0 24 24" fill="#fff"><circle cx="12" cy="5" r="3"/><path d="M7 10h10v5h-2v7h-6v-7H7z"/></svg></div>
    <h3>Lift</h3>
    <p>Protect the people who count on you with plans built for each stage of life.</p>
    <a class="btn">Get a Quote!</a>
  </div>
  <div class="line-card" style="left:380px">
    <div class="line-icon"><svg width="42" height="42" viewBox="0 0 24 24" fill="#fff"><path d="M5 11l2-5h10l2 5h1v7h-2v2h-3v-2H9v2H6v-2H4v-7zm2.5 0h9l-1.3-3.3H8.8z"/><circle cx="7.5" cy="14.5" r="1.3" fill="#1f5fa8"/><circle cx="16.5" cy="14.5" r="1.3" fill="#1f5fa8"/></svg></div>
    <h3>Auto</h3>
    <p>Cover your car, your drivers and your trips with rates that fit your budget.</p>
    <a class="btn">Get a Quote!</a>
  </div>
  <div class="line-card" style="left:612px">
    <div class="line-icon"><svg width="42" height="42" viewBox="0 0 24 24" fill="#fff"><path d="M12 3l10 9h-3v9h-5v-6h-4v6H5v-9H2z"/></svg></div>
    <h3>Home</h3>
    <p>Guard your house and what is inside it from fire, storms, theft and more.</p>
    <a class="btn">Get a Quote!</a>
  </div>
  <div class="line-card" style="left:844px">
    <div class="line-icon"><svg width="40" height="40" viewBox="0 0 24 24" fill="#fff"><path d="M9 4h6v3h6v13H3V7h6zm1.5 1.5V7h3V5.5z"/><rect x="3" y="12" width="18" height="1.4" fill="#1f5fa8"/></svg></div>
    <h3>Business</h3>
    <p>Keep your company running with cover for property, staff and liability claims.</p>
    <a class="btn">Get a Quote!</a>
  </div>
</section>

<section class="quote">
  <div class="agent-card">
    <div class="agent-photo" role="img" aria-label="Portrait photo of the agent"></div>
    <div class="agent-name">Nolan Pierce - Agent</div>
    <div class="agent-phone"><svg width="18" height="18" viewBox="0 0 24 24"><path d="M5 3h4l2 5-2.5 1.5a11 11 0 006 6L16 13l5 2v4a2 2 0 01-2 2A16 16 0 013 5a2 2 0 012-2z" fill="#1f5fa8"/></svg>(555) 240-7316</div>
    <div class="agent-address">418 Maple Crest Ave.<br>Cedar Falls, CA 90511</div>
  </div>
  <form class="quote-form">
    <h2>Get An Instant <span>Insurance Quote.</span></h2>
    <div class="form-grid">
      <div class="field"><label>First Name:</label><div class="input"></div></div>
      <div class="field"><label>Height/Weight:</label><div class="input"></div></div>
      <div class="field"><label>Sex:</label><div class="input">Select<span>▾</span></div></div>
      <div class="field"><label>Tobacco Use:</label><div class="input">Select<span>▾</span></div></div>
      <div class="field"><label>Date of Birth:</label><div class="input-row"><div class="input">Month<span>▾</span></div><div class="input">Day<span>▾</span></div><div class="input">Year<span>▾</span></div></div></div>
      <div class="field"><label>Phone:</label><div class="input"></div></div>
      <div class="field"><label>Current Health:</label><div class="input">Select<span>▾</span></div></div>
      <div class="field"><label>Email:</label><div class="input"></div></div>
    </div>
    <button class="btn" type="button">Submit</button>
  </form>
</section>

<section class="about">
  <h2 class="section-title">About <span>Insurance Agent</span></h2>
  <hr>
  <p>We are a local agency that helps families and owners find the right cover at a fair price. We compare plans from many carriers so you do not have to, and we explain each option in plain words. Tell us what you need and we will send you a quote the same day. Our team stays with you after you sign, helping with claims, changes and renewals whenever life moves on.</p>
</section>

<section class="reviews">
  <div class="reviews-head">
    <span class="round-arrow"><svg width="10" height="14" viewBox="0 0 10 14"><path d="M8 1L2 7l6 6" stroke="#333" stroke-width="2.5" fill="none"/></svg></span>
    <h2 class="section-title">Our Customer <span>Review</span></h2>
    <span class="round-arrow"><svg width="10" height="14" viewBox="0 0 10 14"><path d="M2 1l6 6-6 6" stroke="#333" stroke-width="2.5" fill="none"/></svg></span>
  </div>
  <div class="review" style="left:145px">
    <div class="review-box"><span class="qmark">“</span><p>My agent found me a better home and auto plan in one afternoon and saved me money. Every call was friendly, clear and quick. I would recommend this office to anyone looking for honest advice.</p></div>
    <div class="reviewer"><div class="reviewer-photo" role="img" aria-label="Customer portrait photo"></div><span class="reviewer-name">Mr Owen Caldwell</span></div>
  </div>
  <div class="review" style="left:615px">
    <div class="review-box"><span class="qmark">“</span><p>When a storm hit our roof, the claim was handled fast and without stress. The team kept me updated at each step and the payout came sooner than I expected. Great service all around.</p></div>
    <div class="reviewer"><div class="reviewer-photo" role="img" aria-label="Customer portrait photo"></div><span class="reviewer-name">Mr Owen Caldwell</span></div>
  </div>
</section>

<section class="partners">
  <h2 class="section-title">Insurance <span>Company</span></h2>
  <div class="partner-row">
    <svg width="16" height="22" viewBox="0 0 10 14"><path d="M8 1L2 7l6 6" stroke="#1f5fa8" stroke-width="3" fill="none"/></svg>
    <span class="partner"><i></i>Ledgerly</span>
    <span class="partner"><i></i>Fieldnote</span>
    <span class="partner"><i></i>Ardent</span>
    <span class="partner"><i></i>Northbeam</span>
    <span class="partner"><i></i>Kestrel</span>
    <svg width="16" height="22" viewBox="0 0 10 14"><path d="M2 1l6 6-6 6" stroke="#1f5fa8" stroke-width="3" fill="none"/></svg>
  </div>
</section>

<footer class="site-footer">
  <h4>Disclaimer</h4>
  <p>Insurance products are offered through licensed agents only. Coverage, rates and discounts vary by state and are subject to underwriting. This page gives general information and is not a contract. Please read your policy for full terms, limits and exclusions before you buy.</p>
  <div class="footer-bar"><small>© 2015 Insurance Agent. All Rights Reserved.</small><strong>Insurance Agent</strong></div>
</footer>

</body>
</html>
```